Satchel & Sundial needs new business card design

I need a new business card design. I'm looking for out-of-the-box design which represents the freedom of being a location independent entrepreneur.
I offer coaching, retreats and trips.
I would like to see designs with and without the photo.
Colors I use are black (#000000), green (#25A796) and brown (#D7C38C)
Website satchelandsundial.example

Target Market(s)

location independent entrepreneurs, digital nomads, people looking to swap the 9 to 5 for a lifestyle business

Industry/Entity Type

Business

Contact Information for Business Card

Dorota Falkner
Your Lifestyle Business Coach, Retreat & Trip Leader
http://satchelandsundial.example
hello@satchelandsundial.example
Live a life you don't need a holiday from

Font styles to use
Serif
Sans Serif

Requirements
Must have
• One side should contain only the logo. I would also consider having the "Live a life you don't need a holiday from" on that side too (depending on how it looks)
• Please show both sides on the designs.

```html
<!DOCTYPE html>
<html lang="en">
<head>
<meta charset="utf-8">
<title>Satchel &amp; Sundial — Business Card</title>
<link rel="stylesheet" href="https://fonts.googleapis.com/css2?family=Open+Sans:wght@400;600;700&display=swap">
<style>
  :root {
    --backdrop: #5b5b5c;
    --card-black: #231f20;
    --card-green: #1fae9a;
    --ink-dark: #1b1b1b;
    --ink-white: #ffffff;
    --brand-sand: #d7c38c;
  }
  * { box-sizing: border-box; margin: 0; padding: 0; }
  html, body {
    width: 1200px;
    height: 864px;
    overflow: hidden;
    background: var(--backdrop);
    font-family: "Open Sans", Arial, sans-serif;
  }
  .stage {
    position: relative;
    width: 1200px;
    height: 864px;
  }
  .card {
    position: absolute;
    left: 300px;
    width: 600px;
    height: 343px;
    box-shadow: 0 10px 24px rgba(0, 0, 0, 0.35);
  }
  .card--front {
    top: 68px;
    background: var(--card-black);
    display: flex;
    align-items: center;
    justify-content: center;
  }
  .card--back {
    top: 453px;
    background: var(--card-green);
  }
  .wordmark {
    font-weight: 700;
    color: var(--ink-white);
    text-transform: uppercase;
    letter-spacing: 0.04em;
    line-height: 1;
    white-space: nowrap;
  }
  .card--front .wordmark { font-size: 46px; }
  .card--back .wordmark {
    position: absolute;
    right: 42px;
    top: 124px;
    font-size: 20px;
  }
  .identity {
    position: absolute;
    left: 62px;
    top: 92px;
    color: var(--ink-dark);
  }
  .identity__name {
    font-size: 20px;
    font-weight: 700;
    margin-bottom: 4px;
  }
  .identity__role {
    font-size: 14.5px;
    line-height: 1.3;
    font-weight: 400;
  }
  .divider {
    position: absolute;
    left: 0;
    right: 38px;
    top: 160px;
    height: 1.5px;
    background: var(--ink-white);
  }
  .contact {
    position: absolute;
    left: 62px;
    top: 178px;
    list-style: none;
    color: var(--ink-dark);
    font-size: 14.5px;
    line-height: 1.5;
  }
  .contact__item {
    display: flex;
    align-items: center;
    gap: 10px;
  }
  .contact__icon {
    width: 12px;
    height: 12px;
    flex: none;
  }
  .tagline {
    position: absolute;
    left: 50px;
    top: 266px;
    font-size: 12.5px;
    font-weight: 700;
    text-transform: uppercase;
    color: var(--ink-dark);
    letter-spacing: 0.01em;
  }
</style>
</head>
<body>
<main class="stage">
  <section class="card card--front" aria-label="Business card front">
    <p class="wordmark">Satchel &amp; Sundial</p>
  </section>

  <section class="card card--back" aria-label="Business card back">
    <div class="identity">
      <h1 class="identity__name">Dorota Falkner</h1>
      <p class="identity__role">Your Lifestyle Business Coach<br>Retreat &amp; Trip Leader</p>
    </div>

    <p class="wordmark">Satchel &amp; Sundial</p>

    <div class="divider"></div>

    <ul class="contact">
      <li class="contact__item">
        <svg class="contact__icon" viewBox="0 0 12 12" aria-hidden="true">
          <rect x="0.5" y="2" width="11" height="8" fill="#1b1b1b"/>
          <path d="M0.5 2 L6 6.5 L11.5 2" fill="none" stroke="#1fae9a" stroke-width="1"/>
        </svg>
        hello@satchelandsundial.example
      </li>
      <li class="contact__item">
        <svg class="contact__icon" viewBox="0 0 12 12" aria-hidden="true">
          <circle cx="6" cy="6" r="5.5" fill="#1b1b1b"/>
          <ellipse cx="6" cy="6" rx="2.4" ry="5.5" fill="none" stroke="#1fae9a" stroke-width="0.8"/>
          <line x1="0.5" y1="6" x2="11.5" y2="6" stroke="#1fae9a" stroke-width="0.8"/>
        </svg>
        www.satchelandsundial.example
      </li>
    </ul>

    <p class="tagline">Live a life you don't need a holiday from</p>
  </section>
</main>
</body>
</html>
```